Winter is coming, is your home ready ?

We are a full service Insulation contracting services company . We insulate new and existing homes, commercial and industrial buildings.

We are looking for a billboard that shows our harsh winter approaching and a call to action for getting a free estimate.

We specialize in spray foam insulation but it doesn't need to be called out on the billboard if too much text make it looks too busy.

We do enjoy humor if its something that could work and keep people thinking of us.
Company web site is www.brambowinsulation.com
Company phone number is 555-318-2947

```html
<!DOCTYPE html>
<html lang="en">
<head>
<meta charset="utf-8">
<title>Brambow Insulation – Winter Billboard</title>
<link rel="stylesheet" href="https://fonts.googleapis.com/css2?family=Exo+2:wght@600;700;800&family=Questrial&display=swap">
<style>
  :root {
    --lime: #a3bd1c;
    --ink: #58595b;
    --rule: #6d6e70;
    --paper: #ffffff;
    --stage: #eceff2;
    --wedge: #6a6b6d;
  }
  * { margin: 0; padding: 0; box-sizing: border-box; }
  html, body {
    width: 1200px; height: 780px; overflow: hidden;
    background: var(--stage);
  }
  .billboard {
    position: absolute;
    left: 40px; top: 193px;
    width: 1120px; height: 394px;
    background: var(--paper);
    overflow: hidden;
    box-shadow: 0 4px 18px rgba(0,0,0,.12);
  }
  .billboard__art { position: absolute; inset: 0; }
  .brand {
    position: absolute; left: 28px; top: 30px;
    padding: 8px 14px;
    background: var(--paper);
    font-family: "Exo 2", sans-serif; font-weight: 600;
    font-size: 22px; color: var(--ink); line-height: 1.1;
  }
  .headline {
    position: absolute; left: 440px; width: 680px;
    text-align: center;
  }
  .headline__lead {
    top: 52px;
    font-family: "Questrial", sans-serif; font-weight: 400;
    font-size: 54px; color: var(--ink); line-height: 1;
  }
  .headline__ask {
    top: 118px;
    font-family: "Exo 2", sans-serif; font-weight: 800;
    font-size: 60px; color: var(--lime); line-height: 1;
  }
  .sectors {
    position: absolute; left: 477px; width: 596px; top: 218px; height: 53px;
    border-top: 3px solid var(--rule); border-bottom: 3px solid var(--rule);
    display: flex; align-items: center; justify-content: center; gap: 10px;
    font-family: "Exo 2", sans-serif; font-weight: 600;
    font-size: 33px; color: var(--lime);
  }
  .sectors__divider { color: var(--ink); font-weight: 600; }
  .cta {
    position: absolute; left: 34px; top: 344px; height: 50px;
    display: flex; align-items: center;
    font-family: "Exo 2", sans-serif; font-weight: 700;
    font-size: 28px; color: var(--paper); letter-spacing: .2px;
  }
  .contact {
    position: absolute; left: 560px; top: 344px; height: 50px;
    display: flex; align-items: center;
  }
  .contact__icon { width: 26px; height: 26px; flex: none; }
  .contact__phone {
    margin-left: 6px;
    font-family: "Exo 2", sans-serif; font-weight: 600;
    font-size: 33px; color: var(--lime);
  }
  .contact__sep { width: 1px; height: 36px; background: var(--rule); margin: 0 10px 0 14px; }
  .contact__web {
    margin-left: 6px;
    font-family: "Exo 2", sans-serif; font-weight: 600;
    font-size: 18px; color: var(--ink);
  }
  .contact__web em { font-style: normal; color: var(--lime); }
</style>
</head>
<body>
  <main class="billboard">
    <svg class="billboard__art" viewBox="0 0 1120 394" width="1120" height="394">
      <defs>
        <linearGradient id="snowHouse" x1="0" y1="0" x2="0.4" y2="1">
          <stop offset="0" stop-color="#dfe6ee"/>
          <stop offset="0.45" stop-color="#c7d0da"/>
          <stop offset="0.7" stop-color="#a06a4c"/>
          <stop offset="1" stop-color="#6f6a70"/>
        </linearGradient>
      </defs>
      <polygon class="photo" role="img" aria-label="Photo of a snow-covered house with a wooden gable on a cloudy winter day"
        points="0,0 334,0 487,345 0,345" fill="url(#snowHouse)"/>
      <polygon class="wedge" points="330,0 367,0 354,60" fill="var(--wedge)"/>
      <polygon class="cta-band" points="0,344 538,344 560,394 0,394" fill="var(--lime)"/>
    </svg>

    <div class="brand">Brambow Insulation, Inc.</div>

    <h1 class="headline headline__lead">Winter is coming,</h1>
    <h2 class="headline headline__ask">is your home ready?</h2>

    <p class="sectors">
      <span>Residential</span><span class="sectors__divider">|</span>
      <span>Commercial</span><span class="sectors__divider">|</span>
      <span>Industrial</span>
    </p>

    <p class="cta">CALL FOR GETTING A FREE ESTIMATE</p>

    <div class="contact">
      <svg class="contact__icon" viewBox="0 0 26 26" aria-hidden="true">
        <circle cx="13" cy="13" r="11.5" fill="none" stroke="#58595b" stroke-width="1.6"/>
        <path d="M9 7.5c-1 .6-1.6 1.6-1.2 3 .9 3.2 3.3 5.9 6.6 7.2 1.2.4 2.3 0 3-1l-2.1-2.1-1.5.8c-1.3-.7-2.4-1.8-3-3.1l.8-1.5z" fill="#58595b"/>
      </svg>
      <span class="contact__phone">555-318-2947</span>
      <span class="contact__sep"></span>
      <svg class="contact__icon" viewBox="0 0 26 26" aria-hidden="true">
        <circle cx="13" cy="13" r="11.5" fill="none" stroke="#58595b" stroke-width="1.6"/>
        <circle cx="13" cy="13" r="7" fill="none" stroke="#58595b" stroke-width="1.2"/>
        <ellipse cx="13" cy="13" rx="3" ry="7" fill="none" stroke="#58595b" stroke-width="1.2"/>
        <line x1="6" y1="13" x2="20" y2="13" stroke="#58595b" stroke-width="1.2"/>
      </svg>
      <span class="contact__web">www.<em>brambow</em>insulation.com</span>
    </div>
  </main>
</body>
</html>
```